Erstellung eines Polizeiwimpels für Kinder
Zielgruppe
Wir stellen Fahrradwimpel für Kinder her. Hier finden Sie unsere Produkte: https://www.kaufhalle-wiro.de/laden/regal/58203917462
Aufgabenstellung
Wir möchten einen 'Polizeiwimpel' für Kinder herstellen.
Wenn möglich, nur eine Farbe verwenden (reduziert Kosten in der Produktion). Der Hintergrund soll 'Polizei Blau' sein.
Wimpelgröße: 17,5 cm X 32 cm X 32cm (Dreieckig)
Ich habe ein selbst erstelltes Design hochgeladen. Es soll den Schriftzug 'Polizei' enthalten und evtl. noch 'Polizei Symbole', die Jungs (und ihre Eltern) ansprechen. (Pistole, Sheriffstern, etc.) Das offizielle Wappen oder andere Hoheitssymbole dürfen wir allerdings nicht verwenden.

```html
<!DOCTYPE html>
<html lang="de">
<head>
<meta charset="utf-8">
<title>Polizeiwimpel – vier Varianten</title>
<link rel="stylesheet" href="https://fonts.googleapis.com/css2?family=Arimo:wght@700&display=swap">
<style>
  :root {
    --police-blue: #035ca2;
    --paper: #ffffff;
    --cut-line: #9a9a9a;
    --badge-soft: rgba(255, 255, 255, 0.28);
  }
  html, body {
    margin: 0;
    padding: 0;
    width: 1200px;
    height: 960px;
    overflow: hidden;
    background: var(--paper);
  }
  .sheet {
    display: block;
    width: 1200px;
    height: 960px;
  }
  .pennant-shape { fill: var(--police-blue); }
  .cut-line {
    stroke: var(--cut-line);
    stroke-width: 0.7;
    stroke-dasharray: 1.5 1.5;
    fill: none;
  }
  .badge-solid { fill: var(--paper); }
  .badge-outline { fill: var(--badge-soft); }
  .ribbon-blue { fill: var(--police-blue); }
  .ribbon-white { fill: var(--paper); }
  .ribbon-label {
    font-family: "Arimo", Arial, sans-serif;
    font-weight: 700;
    font-size: 25px;
    text-anchor: middle;
    dominant-baseline: central;
  }
  .ribbon-label--white { fill: var(--paper); }
  .ribbon-label--blue { fill: var(--police-blue); }
  .web-address {
    font-family: "Arimo", Arial, sans-serif;
    font-weight: 700;
    font-size: 7px;
    fill: var(--paper);
  }
</style>
</head>
<body>
<svg class="sheet" viewBox="0 0 1200 960" xmlns="http://www.w3.org/2000/svg">
  <line class="cut-line" x1="609" y1="57" x2="609" y2="888"/>
  <line class="cut-line" x1="40" y1="476" x2="578" y2="476"/>
  <line class="cut-line" x1="632" y1="474" x2="1169" y2="474"/>

  <!-- Wimpel 1: gefüllter Stern -->
  <g class="pennant" transform="translate(59 105)">
    <polygon class="pennant-shape" points="0,0 508,138 0,277"/>
    <g role="img" aria-label="Weißer Sheriffstern mit Punktkranz">
      <circle class="badge-solid" cx="108" cy="138" r="90"/>
    </g>
    <g transform="translate(108 138) rotate(-10)">
      <rect class="ribbon-blue" x="-68" y="-14" width="136" height="28"/>
      <text class="ribbon-label ribbon-label--white" x="0" y="1">POLIZEI</text>
    </g>
    <text class="web-address" transform="translate(17 262) rotate(-15.3)">www.radfahne-kids.de</text>
  </g>

  <!-- Wimpel 2: Stern mit Nahtlinie und Sternchen -->
  <g class="pennant" transform="translate(653 104)">
    <polygon class="pennant-shape" points="0,0 508,139 0,278"/>
    <g role="img" aria-label="Weißer Sheriffstern mit gestrichelter Kontur und kleinen Sternen">
      <circle class="badge-solid" cx="108" cy="138" r="90"/>
    </g>
    <g transform="translate(108 138) rotate(-10)">
      <rect class="ribbon-blue" x="-68" y="-14" width="136" height="28"/>
      <text class="ribbon-label ribbon-label--white" x="0" y="1">POLIZEI</text>
    </g>
    <text class="web-address" transform="translate(17 263) rotate(-15.3)">www.radfahne-kids.de</text>
  </g>

  <!-- Wimpel 3: Konturstern -->
  <g class="pennant" transform="translate(57 559)">
    <polygon class="pennant-shape" points="0,0 509,139 0,278"/>
    <g role="img" aria-label="Sheriffstern als weiße Konturlinie mit Strahlenkranz">
      <circle class="badge-outline" cx="108" cy="140" r="90"/>
    </g>
    <g transform="translate(108 140) rotate(-14)">
      <rect class="ribbon-white" x="-68" y="-15" width="136" height="30"/>
      <text class="ribbon-label ribbon-label--blue" x="0" y="2">POLIZEI</text>
    </g>
    <text class="web-address" transform="translate(17 263) rotate(-15.3)">www.radfahne-kids.de</text>
  </g>

  <!-- Wimpel 4: Konturstern mit Facetten -->
  <g class="pennant" transform="translate(652 561)">
    <polygon class="pennant-shape" points="0,0 508,139 0,278"/>
    <g role="img" aria-label="Sheriffstern als weiße Konturlinie mit Facetten und Punktkranz">
      <circle class="badge-outline" cx="108" cy="140" r="90"/>
    </g>
    <g transform="translate(108 140) rotate(-14)">
      <rect class="ribbon-white" x="-68" y="-15" width="136" height="30"/>
      <text class="ribbon-label ribbon-label--blue" x="0" y="2">POLIZEI</text>
    </g>
    <text class="web-address" transform="translate(17 262) rotate(-15.3)">www.radfahne-kids.de</text>
  </g>
</svg>
</body>
</html>
```